Vantor Apparel - T-Shirts on Storevia

Hi - I'm creating a new site to sell undershirts. The premise of the undershirt is that it has a U-neck shape so that your white undershirt does not show when you are wearing a button shirt. I want the site to be fun but still look stunning because I want to attract a certain clientele (business professionals with a sense of humor). I'm creating a funny video to post on the site to hopefully get some social media buzz.
I want the design to highlight the product but more importantly the lifestyle of the person who wears it. This is an undershirt so nobody really sees it and that's the point.
Since this is a single product that I want to sell, I want to make sure that the design works with Storevia. Since this is not for theme development, this design must work with an existing theme on Storevia (preferably free but if you must then no more than $75). You can choose the theme to design for.
Products:
* Single vantor undershirt in 4 sizes - S, M, L and XL
* 3 packs or 7 packs (buy 6 get 1 free)
* One-time purchase or subscription (delivery every 3 or 6 months) - I know this will require custom theme development
Attached you will find a very rough idea for the site and this was made before I had considered putting in a video (Brix template). It's going to be tough to catch lightning in a bottle much like Penny Razor Guild but that's what I'm hoping for.
Name of the company is Vantor Apparel. Logo attached. Included .ai file which has some funky colors so please use the light blue color logo similar to the png's attached.
Here is the site for a competitor. There's much to be improved on the site but I include it here because the concept of the undershirt is the same: http://www.mirelgarments.example
Feel free to use stock images that I can purchase on the site that represents a young and cool vibe. I will be taking shots of the shirts for the product page so for now use some generic shirt please.
Updates
Project Deadline Extended
Reason: Please take a look at feedback for other designs. I'm hoping for my mockup to be an inspiration, not just re-skinning the mockup I created. Plus it must be based on a Storevia theme. Use stock images as necessary but keep the budget for purchasing images under $100.
Target Market(s)
Male 30-50

```html
<!DOCTYPE html>
<html lang="en">
<head>
<meta charset="utf-8">
<title>Vantor Apparel</title>
<link rel="stylesheet" href="https://fonts.googleapis.com/css2?family=Oswald:wght@400;500;700&family=Open+Sans:wght@400;600;700&display=swap">
<style>
:root{
  --blue:#29a3dd;
  --blue-dark:#1d8cc2;
  --ink:#222;
  --navy:#1e2a38;
  --text:#666;
  --topbar:#1f1c1b;
  --dark:#2f2b2a;
  --dark-panel:#3a3534;
  --footer:#272322;
  --grey-card:#ececec;
  --white:#fff;
}
*{box-sizing:border-box;margin:0;padding:0}
html,body{width:1200px;height:3214px;overflow:hidden}
body{font-family:"Open Sans",Arial,sans-serif;color:var(--text);background:var(--white);position:relative}
.abs{position:absolute}
.heading{font-family:"Oswald",Arial,sans-serif;font-weight:700;text-transform:uppercase;color:var(--ink)}

/* top bar */
.topbar{left:0;top:0;width:1200px;height:48px;background:var(--topbar);color:#ddd;font-size:12px}
.topbar .welcome{left:96px;top:15px}
.topbar .util{right:96px;top:15px;display:flex;gap:34px}
.topbar .util span::before{content:"";display:inline-block;width:9px;height:9px;background:#ddd;border-radius:2px;margin-right:8px;vertical-align:-1px}

/* header */
.header{left:0;top:48px;width:1200px;height:118px;background:var(--white)}
.logo{left:120px;top:38px;font-size:32px;font-weight:600;color:var(--navy);letter-spacing:-.5px}
.nav{right:74px;top:52px;display:flex;gap:38px;font-family:"Oswald",Arial,sans-serif;font-weight:500;font-size:14px;color:var(--ink)}
.nav svg{margin-top:3px}

/* hero */
.hero{left:0;top:166px;width:1200px;height:445px;
  background:
    radial-gradient(ellipse 150px 190px at 300px 330px,#4f7896 0%,rgba(79,120,150,.85) 55%,rgba(79,120,150,0) 100%),
    radial-gradient(ellipse 90px 110px at 320px 110px,#b58c72 0%,rgba(150,110,85,.8) 50%,rgba(120,95,75,0) 100%),
    radial-gradient(ellipse 260px 160px at 1040px 370px,#5f9fb4 0%,rgba(95,159,180,0) 100%),
    radial-gradient(ellipse 300px 140px at 750px 90px,#dfe3d2 0%,rgba(223,227,210,0) 100%),
    linear-gradient(180deg,#c6cdb9 0%,#a8b497 45%,#8a9a7c 75%,#6f7e6a 100%)}
.hero-tag{background:#000;color:var(--white);font-family:"Oswald",Arial,sans-serif;font-weight:700;text-transform:uppercase;text-align:center}
.hero-tag.small{left:710px;top:289px;width:319px;height:50px;font-size:27px;line-height:50px;letter-spacing:1px}
.hero-tag.big{left:683px;top:348px;width:407px;height:81px;font-size:56px;line-height:75px;border:3px solid #fff}
.hero-tag.cta{left:801px;top:437px;width:166px;height:45px;font-size:28px;line-height:45px;letter-spacing:1px}

/* section titles */
.title-box{border:2px solid var(--ink);height:54px;line-height:50px;text-align:center;font-size:21px;letter-spacing:1px}
.title-box.light{border-color:var(--white);color:var(--white)}

/* products */
.intro{left:150px;top:780px;width:900px;text-align:center;font-size:12.5px;line-height:22px}
.read-more{font-family:"Oswald",Arial,sans-serif;font-weight:700;font-size:12px;color:var(--ink);text-transform:uppercase}
.product{width:300px;text-align:center}
.product .shot{margin:0 auto;width:255px;height:282px;
  background:
    radial-gradient(ellipse 95px 120px at 45% 42%,#ffffff 0%,#f7f7f7 60%,rgba(247,247,247,0) 100%),
    radial-gradient(ellipse 100px 115px at 62% 62%,#f1f1f1 0%,rgba(230,230,230,0) 100%),
    #fff}
.product .name{margin-top:24px;font-family:"Oswald",Arial,sans-serif;font-weight:700;font-size:14px;line-height:21px;color:var(--ink);text-transform:uppercase}
.price-row{display:flex;width:212px;height:37px;margin:0 auto;font-family:"Oswald",Arial,sans-serif;font-weight:700;font-size:14px;color:var(--white);text-transform:uppercase}
.price-row .label{flex:1;background:var(--blue);text-align:left;padding-left:14px;line-height:37px}
.price-row .price{width:70px;background:var(--blue-dark);line-height:37px}
.price-row.buy{margin-top:26px}
.price-row.sub{margin-top:12px}
.shop-now{left:482px;top:1420px;width:236px;height:51px;background:var(--blue);color:var(--white);clip-path:polygon(0 0,100% 0,92% 100%,8% 100%);font-family:"Oswald",Arial,sans-serif;font-weight:700;font-size:24px;line-height:51px;text-align:center}

/* blog */
.blog{left:0;top:1543px;width:1200px;height:747px;background:var(--dark)}
.post{width:300px;color:#cfcfcf}
.post .num{display:inline-block;width:43px;height:43px;background:var(--blue);color:var(--white);font-family:"Oswald",Arial,sans-serif;font-weight:700;font-size:26px;line-height:43px;text-align:center;vertical-align:middle}
.post h3{display:inline-block;margin-left:20px;font-family:"Oswald",Arial,sans-serif;font-weight:700;font-size:18px;color:var(--white);text-transform:uppercase;vertical-align:middle;position:relative}
.post h3::after{content:"";position:absolute;left:0;bottom:-10px;width:40px;height:2px;background:var(--white)}
.post p{margin-top:24px;font-size:12px;line-height:20px}
.post .read-more{display:block;margin-top:14px;color:var(--white)}
.promo-left{left:96px;top:2162px;width:408px;height:123px;
  background:
    radial-gradient(ellipse 60px 75px at 90px 70px,#f4f4f4 0%,#e6e6e6 55%,rgba(230,230,230,0) 100%),
    radial-gradient(ellipse 28px 30px at 90px 18px,#b48a70 0%,rgba(180,138,112,0) 100%),
    linear-gradient(90deg,#77726f,#9a9693 60%,#6f6b69)}
.promo-right{left:504px;top:2162px;width:600px;height:123px;background:var(--blue)}
.promo-text{font-family:"Oswald",Arial,sans-serif;font-weight:700;color:var(--white);text-transform:uppercase}
.btn-outline{border:2px solid var(--white);color:var(--white);font-family:"Oswald",Arial,sans-serif;font-weight:700;font-size:13px;text-align:center;text-transform:uppercase}

/* testimonial */
.quote-photo{left:96px;top:2473px;width:285px;height:220px;
  background:
    radial-gradient(ellipse 55px 65px at 150px 95px,#b88f76 0%,rgba(150,112,90,.7) 55%,rgba(120,90,70,0) 100%),
    radial-gradient(ellipse 120px 70px at 150px 210px,#2a2a2a 0%,rgba(42,42,42,0) 100%),
    linear-gradient(135deg,#8b8b8b,#4a4a4a 60%,#2e2e2e)}
.quote-card{left:391px;top:2473px;width:598px;height:220px;background:var(--grey-card);padding:38px 20px}
.quote-card .who{font-family:"Oswald",Arial,sans-serif;font-weight:700;font-size:17px;color:var(--ink);position:relative}
.quote-card .who::after{content:"";position:absolute;left:0;bottom:-9px;width:40px;height:2px;background:var(--ink)}
.quote-card p{margin-top:26px;font-size:12px;line-height:22px}
.arrow{width:42px;height:42px;background:var(--blue)}

/* features */
.features{left:0;top:2759px;width:1200px;height:362px;background:var(--dark)}
.feature{width:334px;height:316px;background:var(--dark-panel);color:#cfcfcf;text-align:center}
.feature .bar{height:94px;background:var(--blue);display:flex;align-items:center;justify-content:center;gap:20px;font-family:"Oswald",Arial,sans-serif;font-weight:700;font-size:19px;color:var(--white);text-transform:uppercase}
.feature .rule{width:44px;height:2px;background:#cfcfcf;margin:26px auto 0}
.feature p{margin:22px auto 0;width:270px;font-size:12px;line-height:21px}
.cards{display:flex;justify-content:center;gap:10px;margin-top:16px}
.cards span{width:52px;height:30px;border-radius:3px;background:#f2f2f2}
.feature .btn-outline{position:absolute;left:100px;bottom:30px;width:134px;height:38px;line-height:34px}

/* footer */
.footer{left:0;top:3121px;width:1200px;height:93px;background:var(--footer);color:#cfcfcf;font-size:12px}
.footer .copy{left:96px;top:38px}
.footer .copy b{color:var(--white)}
.footer .links{left:415px;top:38px;display:flex;gap:26px;text-transform:uppercase}
.footer .social{right:96px;top:33px;display:flex;gap:8px}
.footer .social span{width:27px;height:27px;border-radius:3px}
</style>
</head>
<body>

<div class="abs topbar">
  <span class="abs welcome">Welcome to our online store! Login or Signup</span>
  <div class="abs util"><span>Setting</span><span>My Account</span><span>Cart: 0 item</span></div>
</div>

<header class="abs header">
  <div class="abs logo">vantor Apparel</div>
  <nav class="abs nav">
    <span>HOME</span><span>CATEGORIES</span><span>ABOUT US</span><span>FAQs</span><span>CONTACT US</span>
    <svg width="14" height="14" viewBox="0 0 14 14"><circle cx="6" cy="6" r="4.5" fill="none" stroke="#222" stroke-width="1.8"/><line x1="9.3" y1="9.3" x2="13" y2="13" stroke="#222" stroke-width="2"/></svg>
  </nav>
</header>

<section class="abs hero" role="img" aria-label="Photo of a man in sunglasses and a denim shirt on a sunny roadside beside a teal car"></section>
<div class="abs hero-tag small">Undershirts for the</div>
<div class="abs hero-tag big">Modern Man</div>
<div class="abs hero-tag cta">Buy Now</div>

<div class="abs heading title-box" style="left:455px;top:678px;width:292px">Our New Products</div>
<p class="abs intro">Lorem ipsum dolor sit amet nemo enim ipsam voluptatem quia voluptas sit aspernatur aut odit aut fugit sed quia consequuntur magni dolores eos qui ratione voluptatem sequi nesciunt neque porro quisquam est qui dolorem ipsum quia dolor sit amet</p>
<span class="abs read-more" style="left:564px;top:848px">Read More</span>

<div class="abs product" style="left:131px;top:897px">
  <div class="shot" role="img" aria-label="Photo of a three pack of white undershirts"></div>
  <div class="name">vantor undershirt<br>3 pack of shirts</div>
  <div class="price-row buy"><span class="label">Buy Now</span><span class="price">$15</span></div>
  <div class="price-row sub"><span class="label">Every 6 Month</span><span class="price">$14</span></div>
</div>
<div class="abs product" style="left:450px;top:897px">
  <div class="shot" role="img" aria-label="Photo of a seven pack of white undershirts"></div>
  <div class="name">vantor undershirt<br>buy 6 get 1 free/7 shirts</div>
  <div class="price-row buy"><span class="label">Buy Now</span><span class="price">$78</span></div>
  <div class="price-row sub"><span class="label">Every 6 Month</span><span class="price">$72</span></div>
</div>
<div class="abs product" style="left:769px;top:897px">
  <div class="shot" role="img" aria-label="Photo of a three pack of white undershirts"></div>
  <div class="name">vantor undershirt<br>3 pack of shirts</div>
  <div class="price-row buy"><span class="label">Buy Now</span><span class="price">$15</span></div>
  <div class="price-row sub"><span class="label">Every 6 Month</span><span class="price">$14</span></div>
</div>
<div class="abs shop-now">SHOP NOW</div>

<section class="abs blog">
  <div class="abs heading title-box light" style="left:429px;top:72px;width:343px">Lates News From Blog</div>

  <article class="abs post" style="left:96px;top:190px"><span class="num">1</span><h3>Amet Voluptatem</h3><p>Lorem ipsum dolor sit amet nemo enim ipsam voluptatem quia voluptas sit aspernatur aut odit aut fugit sed quia consequuntur magni</p><span class="read-more">Read More</span></article>
  <article class="abs post" style="left:450px;top:190px"><span class="num">2</span><h3>Amet Voluptatem</h3><p>Lorem ipsum dolor sit amet nemo enim ipsam voluptatem quia voluptas sit aspernatur aut odit aut fugit sed quia consequuntur magni</p><span class="read-more">Read More</span></article>
  <article class="abs post" style="left:806px;top:190px"><span class="num">3</span><h3>Amet Voluptatem</h3><p>Lorem ipsum dolor sit amet nemo enim ipsam voluptatem quia voluptas sit aspernatur aut odit aut fugit sed quia consequuntur magni</p><span class="read-more">Read More</span></article>
  <article class="abs post" style="left:96px;top:399px"><span class="num">4</span><h3>Amet Voluptatem</h3><p>Lorem ipsum dolor sit amet nemo enim ipsam voluptatem quia voluptas sit aspernatur aut odit aut fugit sed quia consequuntur magni</p><span class="read-more">Read More</span></article>
  <article class="abs post" style="left:450px;top:399px"><span class="num">5</span><h3>Amet Voluptatem</h3><p>Lorem ipsum dolor sit amet nemo enim ipsam voluptatem quia voluptas sit aspernatur aut odit aut fugit sed quia consequuntur magni</p><span class="read-more">Read More</span></article>
  <article class="abs post" style="left:806px;top:399px"><span class="num">6</span><h3>Amet Voluptatem</h3><p>Lorem ipsum dolor sit amet nemo enim ipsam voluptatem quia voluptas sit aspernatur aut odit aut fugit sed quia consequuntur magni</p><span class="read-more">Read More</span></article>
</section>

<div class="abs promo-left" role="img" aria-label="Photo of a man wearing a plain white t-shirt against a concrete wall"></div>
<div class="abs promo-text" style="left:257px;top:2200px;font-size:20px;line-height:24px">Buy 6 get 1<br>free</div>
<div class="abs btn-outline" style="left:384px;top:2208px;width:101px;height:42px;line-height:38px">Shop Now</div>
<div class="abs promo-right"></div>
<div class="abs promo-text" style="left:536px;top:2197px;font-size:24px;line-height:27px">One - Time purchase or subscription<br>delivery every 3 or 6 months</div>
<div class="abs btn-outline" style="left:965px;top:2208px;width:102px;height:42px;line-height:38px">Shop Now</div>

<div class="abs heading title-box" style="left:472px;top:2357px;width:257px">What They Says</div>
<div class="abs quote-photo" role="img" aria-label="Portrait photo of a young customer in a dark jacket"></div>
<div class="abs quote-card">
  <div class="who">JOHN DOE, 25 YO</div>
  <p>Lorem ipsum dolor sit amet nemo enim ipsam voluptatem quia voluptas sit aspernatur aut odit aut fugit sed quia consequuntur magni dolores eos qui ratione voluptatem sequi nesciunt neque porro quisquam</p>
</div>
<svg class="abs arrow" style="left:1010px;top:2474px" viewBox="0 0 42 42"><polyline points="25,12 16,21 25,30" fill="none" stroke="#fff" stroke-width="3"/></svg>
<svg class="abs arrow" style="left:1059px;top:2474px" viewBox="0 0 42 42"><polyline points="17,12 26,21 17,30" fill="none" stroke="#fff" stroke-width="3"/></svg>

<section class="abs features">
  <div class="abs feature" style="left:96px;top:6px">
    <div class="bar"><svg width="30" height="30" viewBox="0 0 30 30"><rect x="3" y="7" width="22" height="16" rx="2" fill="none" stroke="#fff" stroke-width="2.5"/><rect x="3" y="11" width="22" height="3" fill="#fff"/></svg>Payment Method</div>
    <div class="rule"></div>
    <p>Lorem ipsum dolor sit amet nemo enim</p>
    <div class="cards"><span></span><span></span><span></span><span></span></div>
    <div class="btn-outline">Read More</div>
  </div>
  <div class="abs feature" style="left:433px;top:6px">
    <div class="bar"><svg width="36" height="28" viewBox="0 0 36 28"><rect x="1" y="5" width="21" height="15" fill="#fff"/><path d="M22 10h7l5 6v4H22z" fill="#fff"/><circle cx="8" cy="22" r="4" fill="#fff" stroke="#29a3dd" stroke-width="2"/><circle cx="28" cy="22" r="4" fill="#fff" stroke="#29a3dd" stroke-width="2"/></svg>Free Shipping</div>
    <div class="rule"></div>
    <p>Lorem ipsum dolor sit amet nemo enim ipsam voluptatem quia voluptas sit aspernatur aut odit</p>
    <div class="btn-outline">Read More</div>
  </div>
  <div class="abs feature" style="left:770px;top:6px">
    <div class="bar"><svg width="26" height="32" viewBox="0 0 26 32"><path d="M7 14V9a6 6 0 0 1 12 0v5" fill="none" stroke="#fff" stroke-width="3"/><rect x="3" y="14" width="20" height="16" rx="2" fill="#fff"/></svg>Secure Shopping</div>
    <div class="rule"></div>
    <p>Lorem ipsum dolor sit amet nemo enim ipsam voluptatem quia voluptas sit aspernatur aut odit</p>
    <div class="btn-outline">Read More</div>
  </div>
</section>

<footer class="abs footer">
  <span class="abs copy">© 2014 <b>YOUR COMPANY</b>. ALL RIGHTS RESERVED.</span>
  <div class="abs links"><span>About Us</span><span>Term and Use</span><span>Privacy Policy</span><span>FAQs</span><span>Contact Us</span></div>
  <div class="abs social">
    <span style="background:#3b5a9a"></span><span style="background:#2aa9e0"></span><span style="background:#d9342b"></span><span style="background:#1f7bb6"></span><span style="background:#cb2027"></span>
  </div>
</footer>

</body>
</html>
```